Exclusive beauty salon needs a price list or services booklet

I need a new very attractive flyer for my beauty salon, containing information on the different services and their prices.
In attachment you can find a pdf of the "old" one, but I'd love to have a beautifully designed new one!
I'd love to have a booklet in format 148 x 148 mm, or in US format, containing 12 or 16 pages, but if you can offer other nice looking designs they are welcome!
The services that need to come in the booklet with their prices can all be found on my website: www.atelierverano.be, starting with
Gelaatsverzorging
Wimperverlenging
Suikerontharing
Wimperlifting
Permanente Make Up
Airbrush Tanning

Target Market(s)

woman from 20 to 89 years old

Industry/Entity Type

Beauty Salon

Font styles to use
Sans Serif

Colors

Designer to choose colors to be used in the design.

Requirements
Must have
• a classy nice look, it must contain details about the services from my beauty salon and their prices, and nice pictures.
• The Names, prices and explanations of the services can easily be found on my website: www.atelierverano.be
Nice to have
• In attachment you can find the "old" price list in pdf, what I need now is a "new booklet" with the new logo and updated services price list.
• I need a very nice and attractive looking booklet, classy chique, Paris chique, looking very expensive.
Should not have
• Not too much colors, not too curly, but still feminine

```html
<!DOCTYPE html>
<html lang="nl">
<head>
<meta charset="utf-8">
<title>Gelaatsverzorging – Atelier Verano</title>
<link href="https://fonts.googleapis.com/css2?family=Lora:wght@400;600;700&family=Quicksand:wght@400;500&display=swap" rel="stylesheet">
<style>
  :root{
    --canvas:#e6e6e6;
    --paper:#f5f4f4;
    --ink:#1c1c1c;
    --body:#3a3a3a;
    --rose:#d69aa1;
    --rose-deep:#c98790;
    --blush-1:#f6e9ea;
    --blush-2:#ecccd0;
    --blush-3:#dfb2b8;
    --rule:#e3cfd2;
  }
  *{box-sizing:border-box;margin:0;padding:0}
  html,body{width:1200px;height:900px;overflow:hidden;background:var(--canvas)}
  .spread{position:absolute;left:50px;top:175px;width:1100px;height:550px;display:flex}
  .page{position:relative;width:550px;height:550px;overflow:hidden}
  .page--left{background:var(--paper)}
  .title{position:absolute;top:40px;left:0;right:0;text-align:center;
    font-family:"Lora",serif;font-weight:400;font-size:28px;color:var(--ink)}
  .title-rule{position:absolute;top:88px;left:245px;width:60px;height:2px;background:var(--rose)}
  .subtitle{position:absolute;top:103px;left:0;right:0;text-align:center;
    font-family:"Quicksand",sans-serif;font-size:14px;color:var(--ink)}
  .quote{position:absolute;top:128px;left:70px;right:70px;text-align:center;
    font-family:"Quicksand",sans-serif;font-size:16px;line-height:1.3;color:var(--rose)}
  .product-shot{position:absolute;left:30px;top:205px;width:265px;height:250px;
    background:radial-gradient(ellipse at 32% 50%,#f2c3c8 0 22%,transparent 45%),
               radial-gradient(ellipse at 70% 50%,#c8e2cc 0 22%,transparent 45%),
               var(--paper)}
  .intro{position:absolute;left:313px;top:232px;width:178px;
    font-family:"Quicksand",sans-serif;font-size:11px;line-height:2.05;color:var(--body);text-align:justify}
  .intro p+p{margin-top:18px}
  .folio{position:absolute;left:48px;top:495px;width:442px;border-top:1px solid var(--rule);
    padding-top:6px;display:flex;align-items:center;gap:10px;
    font-family:"Quicksand",sans-serif;font-size:12px;color:var(--rose)}
  .folio-number{width:24px;height:22px;background:var(--rose);color:#fff;
    display:flex;align-items:center;justify-content:center;font-size:11px}
  .page--right{background:var(--blush-1)}
  .backdrop{position:absolute;inset:0;
    background:linear-gradient(90deg,var(--blush-2) 0%,var(--blush-1) 30%,#fbf5f5 55%,var(--blush-1) 100%)}
  .portrait{position:absolute;left:215px;top:0;width:335px;height:550px;
    background:radial-gradient(ellipse at 55% 38%,#f1d6cc 0 28%,transparent 52%),
               radial-gradient(ellipse at 80% 60%,#9a6a4c 0 20%,transparent 50%),
               linear-gradient(180deg,#eed7d3,#e9cfc6)}
  .benefits{position:absolute;left:48px;top:277px;width:200px;font-family:"Quicksand",sans-serif}
  .benefits-title{font-family:"Lora",serif;font-weight:700;font-size:14px;line-height:1.3;color:var(--ink);margin-bottom:12px}
  .benefits ul{list-style:none}
  .benefits li{display:flex;align-items:center;gap:8px;font-size:10px;color:var(--ink);margin-bottom:13px}
  .benefits svg{flex:none}
</style>
</head>
<body>
  <main class="spread">
    <section class="page page--left">
      <h1 class="title">Gelaatsverzorging</h1>
      <div class="title-rule"></div>
      <p class="subtitle">Gelaatsverzorging met de kwalitatieve producten van lumeau</p>
      <p class="quote">"Een antwoord bieden voor iedere huidconditie, omdat deze uniek is"</p>
      <div class="product-shot" role="img" aria-label="Twee flacons gezichtsverzorging, roze en groen, met bloemen en water"></div>
      <div class="intro">
        <p>Het merk Lumeau heeft een uitgebreid aanbod aan gelaatsverzorgingen, geschikt voor alle "huidproblemen".</p>
        <p>Na een persoonlijke huidanalyse wordt een verzorging uitgevoerd die bij u past. Naast de cabineverzorgingen, kan je ook advies krijgen voor de dagelijkse verzorging thuis.</p>
      </div>
      <footer class="folio"><span class="folio-number">1</span>Gelaatsverzorging</footer>
    </section>
    <section class="page page--right">
      <div class="backdrop"></div>
      <div class="portrait" role="img" aria-label="Portretfoto van een vrouw met lang bruin haar en een stralende huid"></div>
      <div class="benefits">
        <h2 class="benefits-title">Gelaatsverzorgingen van<br>Lumeau bieden:</h2>
        <ul>
          <li><svg width="9" height="8" viewBox="0 0 9 8"><path d="M1 4.2 3.4 6.5 8 1.2" fill="none" stroke="#1c1c1c" stroke-width="1.8"/></svg>een combinatie van plezier en welzijn</li>
          <li><svg width="9" height="8" viewBox="0 0 9 8"><path d="M1 4.2 3.4 6.5 8 1.2" fill="none" stroke="#1c1c1c" stroke-width="1.8"/></svg>een unieke ervaring voor de zintuigen</li>
          <li><svg width="9" height="8" viewBox="0 0 9 8"><path d="M1 4.2 3.4 6.5 8 1.2" fill="none" stroke="#1c1c1c" stroke-width="1.8"/></svg>resultaatgerichte behandelingen</li>
        </ul>
      </div>
    </section>
  </main>
</body>
</html>
```